Dynamic Business Card for Sports Supplements Company

Hi! I'm looking for an awesome business card to match my existing sports supplement company. I have uploaded my current company logo and screenshot of the front page of my website.

I would like to have something dynamic and interesting and utilize the colors in the website - the reds and purples

The business card should be double sided and focus on a unique eye-catching design on the back and include all the relevant company info.

Most importantly, it should say somewhere: "Sign up on our website for a coupon code."

Target Market(s)

Mostly for women gym goers but it shouldn't be too feminine. It should be in keeping with the website design. It should flow and clearly be connected to it

Industry/Entity Type

Business

Contact Information for Business Card

Lorraine K. Vestal
CEO
LVestal@Quorvanexco.com
www.quorvanexco.com
555.417.3820
P.O. Box 47315
Marlowe Springs, Ohio 00000

Sign up on our website for a coupon code

Font styles to use
Serif
Sans Serif
Other font styles liked:
• Novecento font family and "Quorvanex" is in AR Destine font

Requirements
Must have
• One side should be a bold Quorvanex logo design. Even just the symbol itself may be o.k. (see attached file)

```html
<!DOCTYPE html>
<html lang="en">
<head>
<meta charset="utf-8">
<title>Quorvanex Business Card</title>
<link href="https://fonts.googleapis.com/css2?family=Open+Sans:wght@400;600;800&display=swap" rel="stylesheet">
<style>
  :root {
    --stage: #d9d9d9;
    --card-dark: #222427;
    --card-mid: #33363a;
    --ink: #ffffff;
    --accent: #e3262c;
  }
  * { margin: 0; padding: 0; box-sizing: border-box; }
  html, body { width: 1200px; height: 880px; overflow: hidden; }
  body {
    background: var(--stage);
    font-family: "Open Sans", sans-serif;
    color: var(--ink);
    display: flex;
    flex-direction: column;
    align-items: center;
    justify-content: center;
    gap: 40px;
  }
  .card {
    width: 700px;
    height: 400px;
    border-radius: 18px;
    background: radial-gradient(ellipse at 40% 35%, var(--card-mid) 0%, var(--card-dark) 75%);
    box-shadow: 0 10px 24px rgba(0,0,0,0.35);
    position: relative;
    overflow: hidden;
  }
  .brand {
    display: flex;
    align-items: center;
    gap: 14px;
  }
  .brand-mark {
    width: 30px;
    height: 30px;
    background: var(--accent);
    flex: none;
  }
  .brand-name {
    font-weight: 800;
    font-size: 50px;
    letter-spacing: 1px;
    text-transform: uppercase;
    color: var(--ink);
    white-space: nowrap;
  }

  /* Front */
  .card-front {
    display: flex;
    flex-direction: column;
    align-items: center;
    padding-top: 130px;
  }
  .signup {
    margin-top: 95px;
    font-size: 21px;
    font-weight: 400;
    white-space: nowrap;
  }
  .signup .highlight { color: var(--accent); }

  /* Back */
  .card-back {
    display: flex;
    align-items: center;
  }
  .card-back .brand-panel {
    width: 350px;
    display: flex;
    justify-content: center;
    padding-top: 80px;
  }
  .card-back .brand-name { font-size: 34px; }
  .card-back .brand-mark { width: 22px; height: 22px; }
  .divider {
    width: 2px;
    height: 230px;
    background: var(--accent);
    flex: none;
  }
  .contact {
    padding-left: 30px;
    font-size: 17px;
    line-height: 1.45;
    white-space: nowrap;
  }
  .contact-name {
    color: var(--accent);
    font-weight: 800;
    font-size: 25px;
    line-height: 1.1;
  }
  .contact-role { margin-bottom: 8px; }
  .contact .label { color: var(--accent); font-weight: 600; }
  .contact .site-name { color: var(--accent); }
  .contact-address { margin-top: 10px; }
</style>
</head>
<body>
  <section class="card card-front">
    <div class="brand">
      <span class="brand-mark"></span>
      <span class="brand-name">Quorvanex</span>
    </div>
    <p class="signup"><span class="highlight">Sign up</span> on our website for a coupon code</p>
  </section>

  <section class="card card-back">
    <div class="brand-panel">
      <div class="brand">
        <span class="brand-mark"></span>
        <span class="brand-name">Quorvanex</span>
      </div>
    </div>
    <div class="divider"></div>
    <div class="contact">
      <p class="contact-name">Lorraine K. Vestal</p>
      <p class="contact-role">CEO</p>
      <p><span class="label">P:</span> 555.417.3820</p>
      <p><span class="label">E:</span> LVestal@Quorvanexco.com</p>
      <p><span class="label">W:</span> www.<span class="site-name">quorvanexco</span>.com</p>
      <p class="contact-address">P.O. Box 47315<br>Marlowe Springs, Ohio 00000</p>
    </div>
  </section>
</body>
</html>
```